update of B2B website and conversion to single page

The current website needs to be modernized. I want what is commonly called a single page website. It is not actually a single page. See some examples here:
https://www.plivenor.example/
https://www.quorbel.example/
https://www.trindavex.example/
Most or all graphics will be replaced.
Please see the attached spreadsheet for a rough draft of the home page layout. Convert the existing website at https://www.zolvarin.example/ to a single page website. We will provide the page content. You will provide all of the design, graphics, development, production deployment. etc. The look and feel should be corporate, polished, premium.

```html
<!DOCTYPE html>
<html lang="en">
<head>
<meta charset="utf-8">
<title>Zolvarin Data – Enterprise Data Quality</title>
<link href="https://fonts.googleapis.com/css2?family=Mulish:wght@400;600;700;800&display=swap" rel="stylesheet">
<style>
:root{
  --navy:#1b2163;
  --footer:#0f1b5e;
  --text:#2b2b33;
  --muted:#6c7080;
  --gold:#f6b81c;
  --panel:#e6e6e6;
  --line:#b9b9b9;
  --white:#ffffff;
}
*{box-sizing:border-box;margin:0;padding:0}
html,body{width:1200px;height:2514px;overflow:hidden;background:var(--white)}
body{position:relative;font-family:'Mulish',sans-serif;color:var(--text)}
.abs{position:absolute}
ul{list-style:none}

/* header */
.site-header{position:absolute;top:0;left:0;width:1200px;height:90px;background:var(--white)}
.brand{position:absolute;left:145px;top:22px;display:flex;align-items:center;gap:12px}
.brand-dot{width:34px;height:34px;border-radius:50%;background:var(--gold)}
.brand-name{font-size:30px;font-weight:700;color:var(--navy);line-height:1}
.brand-tag{position:absolute;left:46px;top:38px;font-size:11px;font-weight:600;color:var(--navy);white-space:nowrap}
.header-phone{position:absolute;right:145px;top:14px;font-size:20px;color:#111;display:flex;align-items:center;gap:6px}
.main-nav{position:absolute;right:145px;top:56px;display:flex;gap:43px;font-size:17px;color:#4a4a55}
.main-nav .active{color:var(--navy);font-weight:600}

/* hero */
.hero{position:absolute;top:90px;left:0;width:1200px;height:525px;
  background:radial-gradient(ellipse 420px 300px at 600px 200px,#cfe3f4 0%,#9cb6cc 45%,#7f8d9b 100%)}
.hero-title{position:absolute;top:40px;width:1200px;text-align:center;font-size:34px;font-weight:700;line-height:40px;color:var(--navy)}
.hero-arrow{position:absolute;top:250px;width:28px;height:28px;background:#2a2a2a;display:flex;align-items:center;justify-content:center}

/* features */
.features{position:absolute;top:615px;left:0;width:1200px;height:318px}
.feature{position:absolute;top:80px}
.feature h3{margin-top:8px;font-size:22px;font-weight:700;color:var(--navy)}
.bullets li{font-size:12.5px;line-height:24px;padding-left:14px;position:relative;color:var(--text)}
.bullets li::before{content:"";position:absolute;left:2px;top:10px;width:4px;height:4px;border-radius:50%;background:var(--text)}

/* connectors */
.connectors{position:absolute;top:933px;left:0;width:1200px;height:437px;
  background:linear-gradient(100deg,#e7a41f 0%,#f7c33c 40%,#f5b62c 65%,#e69a1d 100%)}
.section-title{position:absolute;width:1200px;text-align:center;font-size:33px;font-weight:700;color:var(--navy)}
.card{position:absolute;top:135px;width:292px;height:224px;background:var(--white);padding:18px 14px}
.card h4{font-size:21px;font-weight:700;color:var(--navy);margin-bottom:10px}

/* support */
.support-panel{position:absolute;top:1497px;left:144px;width:912px;height:301px}
.support-list{position:absolute;left:0;top:0;width:456px;height:301px;background:var(--panel)}
.support-item{position:absolute;left:40px}
.support-item h5{position:absolute;left:36px;top:-4px;font-size:22px;font-weight:700;color:var(--navy);white-space:nowrap}
.support-item p{position:absolute;left:36px;font-size:12.5px;line-height:21px;white-space:nowrap}
.support-photo{position:absolute;left:456px;top:0;width:456px;height:301px;
  background:linear-gradient(90deg,#1f1c17 0%,#4a4336 45%,#86826f 75%,#5e5a50 100%)}

/* contact */
.field{position:absolute;height:37px;border:1px solid var(--line);background:var(--white);font-size:12.5px;color:#555;padding:11px 14px}
.submit{position:absolute;left:548px;top:2137px;width:104px;height:44px;background:var(--gold);color:var(--navy);font-size:16px;font-weight:700;display:flex;align-items:center;justify-content:center}

/* footer */
.site-footer{position:absolute;top:2261px;left:0;width:1200px;height:253px;background:var(--footer);color:#aab0d4}
.footer-head{position:absolute;top:44px;font-size:16px;font-weight:700;color:var(--white)}
.footer-text{position:absolute;font-size:12.5px;color:#9aa2cf}
.social{position:absolute;top:84px;width:32px;height:32px;border-radius:50%;background:#7f87b4}
.footer-rule{position:absolute;top:181px;left:144px;width:912px;height:1px;background:#3a4680}
.copyright{position:absolute;top:206px;width:1200px;text-align:center;font-size:12.5px;color:#9aa2cf}
</style>
</head>
<body>

<header class="site-header">
  <div class="brand"><span class="brand-dot"></span><span class="brand-name">Zolvarin Data</span><span class="brand-tag">Enterprise Data Quality Made Easy</span></div>
  <div class="header-phone">
    <svg width="16" height="16" viewBox="0 0 24 24"><path fill="#111" d="M6.6 10.8a15.1 15.1 0 0 0 6.6 6.6l2.2-2.2c.3-.3.7-.4 1-.2 1.1.4 2.3.6 3.6.6.6 0 1 .4 1 1V20c0 .6-.4 1-1 1A17 17 0 0 1 3 4c0-.6.4-1 1-1h3.5c.6 0 1 .4 1 1 0 1.3.2 2.5.6 3.6.1.3 0 .7-.2 1z"/></svg>
    (555) 013-4593
  </div>
  <nav class="main-nav"><span class="active">Welcome</span><span>Services</span><span>Rich Connectors</span><span>Support</span><span>Contact Us</span></nav>
</header>

<section class="hero" role="img" aria-label="Photo of a person working on a laptop at a wooden desk, seen from above, with a network of connected points and a cloud symbol overlaid">
  <h1 class="hero-title">Enterprise Data Quality and<br>Master Data Management Made Easy</h1>
  <div class="hero-arrow" style="left:0"><svg width="14" height="14" viewBox="0 0 14 14"><path d="M13 7H2M6 3L2 7l4 4" stroke="#fff" stroke-width="2" fill="none"/></svg></div>
  <div class="hero-arrow" style="right:0"><svg width="14" height="14" viewBox="0 0 14 14"><path d="M1 7h11M8 3l4 4-4 4" stroke="#fff" stroke-width="2" fill="none"/></svg></div>
</section>

<section class="features">
  <div class="feature" style="left:144px">
    <svg width="54" height="50" viewBox="0 0 54 50">
      <circle cx="20" cy="28" r="13" fill="none" stroke="var(--navy)" stroke-width="8" stroke-dasharray="5 3.2"/>
      <circle cx="20" cy="28" r="9" fill="var(--navy)"/><circle cx="20" cy="28" r="4" fill="#fff"/>
      <circle cx="42" cy="12" r="7" fill="none" stroke="var(--navy)" stroke-width="5" stroke-dasharray="3 2"/>
      <circle cx="42" cy="12" r="2.5" fill="var(--navy)"/>
      <circle cx="42" cy="38" r="7" fill="none" stroke="var(--navy)" stroke-width="5" stroke-dasharray="3 2"/>
      <circle cx="42" cy="38" r="2.5" fill="var(--navy)"/>
    </svg>
    <h3>Easy</h3>
    <ul class="bullets"><li>Cleanse addresses in 5 minutes</li><li>Match and Merge records in 10 minutes</li><li>Master records in 60 minutes</li></ul>
  </div>
  <div class="feature" style="left:491px">
    <svg width="50" height="50" viewBox="0 0 50 50" fill="var(--navy)">
      <rect x="0" y="6" width="8" height="8"/><rect x="13" y="7" width="36" height="6"/>
      <rect x="0" y="21" width="8" height="8"/><rect x="13" y="22" width="36" height="6"/>
      <rect x="0" y="36" width="8" height="8"/><rect x="13" y="37" width="36" height="6"/>
    </svg>
    <h3>Data Quality</h3>
    <ul class="bullets"><li>Global Address Verification</li><li>Data Cleansing/Enrichment</li><li>Match and Merge</li></ul>
  </div>
  <div class="feature" style="left:795px">
    <svg width="44" height="50" viewBox="0 0 44 50" fill="var(--navy)">
      <ellipse cx="22" cy="7" rx="21" ry="7"/>
      <path d="M1 12c0 4 9 7 21 7s21-3 21-7v9c0 4-9 7-21 7S1 25 1 21z"/>
      <path d="M1 25c0 4 9 7 21 7s21-3 21-7v9c0 4-9 7-21 7S1 38 1 34z"/>
      <path d="M1 38c0 4 9 7 21 7s21-3 21-7v5c0 4-9 7-21 7S1 47 1 43z"/>
    </svg>
    <h3>Master Data Management</h3>
    <ul class="bullets"><li>Integration</li><li>Mastering</li><li>Governance</li></ul>
  </div>
</section>

<section class="connectors" role="img" aria-label="Photo of server racks in a data centre with a warm amber tint">
  <h2 class="section-title" style="top:70px">Rich Connectors</h2>
  <div class="card" style="left:144px"><h4>Applications</h4>
    <ul class="bullets"><li>Trindavex CRM</li><li>Servora</li><li>Kelbrin</li><li>Orvane Business Suite</li><li>Mercant Dynamo*</li><li>Saplio*</li></ul></div>
  <div class="card" style="left:454px"><h4>Databases</h4>
    <ul class="bullets"><li>Orvane DB</li><li>MyraSQL</li><li>Mercant QueryStore</li><li>PostlineSQL</li><li>Ibrix Tabula</li><li>Teravolt*</li></ul></div>
  <div class="card" style="left:764px"><h4>Files</h4>
    <ul class="bullets"><li>CSV</li><li>Delimited</li><li>Cellsheet</li><li>* Coming Soon</li></ul></div>
</section>

<h2 class="section-title" style="top:1438px">Support</h2>
<div class="support-panel">
  <div class="support-list">
    <div class="support-item" style="top:40px">
      <svg width="22" height="22" viewBox="0 0 22 22"><circle cx="11" cy="11" r="8.5" fill="none" stroke="var(--navy)" stroke-width="3"/><path d="M11 6v5H8" stroke="var(--navy)" stroke-width="2.5" fill="none"/></svg>
      <h5>Batch</h5><p style="top:28px">On your schedule</p>
    </div>
    <div class="support-item" style="top:120px">
      <svg width="22" height="22" viewBox="0 0 22 22" fill="none" stroke="var(--navy)" stroke-width="3"><path d="M3.5 9a8 8 0 0 1 14.5-2.5"/><path d="M18.5 13a8 8 0 0 1-14.5 2.5"/><path d="M19 2v6h-6" stroke-width="2.5"/><path d="M3 20v-6h6" stroke-width="2.5"/></svg>
      <h5>Streaming</h5><p style="top:28px">Always in sync</p>
    </div>
    <div class="support-item" style="top:200px">
      <svg width="22" height="22" viewBox="0 0 22 22"><circle cx="9" cy="9" r="6.5" fill="none" stroke="var(--navy)" stroke-width="3"/><path d="M14 14l6 6" stroke="var(--navy)" stroke-width="3.5"/></svg>
      <h5>Real Time/Interactive</h5><p style="top:28px">Autocomplete Anything<br>Smart Search</p>
    </div>
  </div>
  <div class="support-photo" role="img" aria-label="Photo of a technician holding a hardware unit beside server racks"></div>
</div>

<h2 class="section-title" style="top:1866px">Contact Us</h2>
<div class="field" style="left:144px;top:1927px;width:218px">Name</div>
<div class="field" style="left:375px;top:1927px;width:218px">Email</div>
<div class="field" style="left:606px;top:1927px;width:218px">Phone</div>
<div class="field" style="left:837px;top:1927px;width:219px">Service for
  <svg class="abs" style="right:12px;top:15px" width="10" height="6" viewBox="0 0 10 6"><path d="M0 0h10L5 6z" fill="#444"/></svg></div>
<div class="field" style="left:144px;top:1988px;width:912px;height:125px;padding:14px 4px">Message</div>
<div class="submit">SUBMIT</div>

<footer class="site-footer">
  <div class="footer-head" style="left:144px">CONTACT INFO</div>
  <div class="footer-text" style="left:144px;top:84px">Phone : 555 010 6548</div>
  <div class="footer-text" style="left:144px;top:109px">Email : info@zolvarin.example</div>
  <div class="footer-head" style="left:511px">LINKS</div>
  <div class="footer-text" style="left:511px;top:84px">Welcome</div>
  <div class="footer-text" style="left:511px;top:109px">Services</div>
  <div class="footer-text" style="left:511px;top:135px">Rich Connectors</div>
  <div class="footer-text" style="left:631px;top:84px">Support</div>
  <div class="footer-text" style="left:631px;top:109px">Contact Us</div>
  <div class="footer-head" style="left:931px">FOLLOW US ON</div>
  <div class="social" style="left:932px"></div>
  <div class="social" style="left:974px"></div>
  <div class="footer-rule"></div>
  <div class="copyright">Copyright © 2018 Zolvarin Data. All rights reserved.</div>
</footer>

</body>
</html>
```